Redesign Comparisson chart - make modern and effective

Use your imaginations to make a powerful distinction between KMV & other holistic modalities. There are 7 elements physical, mental, emotional, energetic, subconscious, superconscious and before and after testing.
We want it to be obvious that KMV is the only modality that works on all these elements simultaneously. We do not want to include any chakras as we want this information to be accepted by a wide range of people and belief systems.'

We want it to look simple but effective. Professional but powerful. We want KMV to stand out even of you eye just passed over i.
Updates

Hi everyone, thanks for your submissions so far. Basically what this image is meant to represent is a comparison chart between all the modalities There are 5 elements physical, mental, emotional, subconscious and superconscious. we want to reflect that KMV is the only modality that works on all these elements simultaneously. As we want the concept to be accepted and not considered woo woo, we want to steer away from chakras.

Target Market(s)

Professionals

Industry/Entity Type

Professional services

Font styles to use
Sans Serif
Other font styles liked:
• Poppins Monserratt

Colors
0094D4
00A9DD
6FCCEA
C7EBF8
E9F6FB

Requirements
Must have
• Clear/professional and clean look. Brand colours and logos. All typography and formats must be cohesive.
Nice to have
• More easy to read, different layout
Should not have
• Do not change the data just the way its presented. No chakras

```html
<!DOCTYPE html>
<html lang="en">
<head>
<meta charset="utf-8">
<title>KMV – Modality Comparison</title>
<link href="https://fonts.googleapis.com/css2?family=Poppins:wght@400;500;600&display=swap" rel="stylesheet">
<style>
:root{
  --brand:#33b5e5;
  --pink:#d575ad;
  --purple:#8670ad;
  --yellow:#e8d152;
  --orange:#f0a036;
  --green:#62b047;
  --sky:#62bfdd;
  --red:#dc4a41;
  --track:#e1e5ee;
  --teal:#1a5670;
  --panel:#f1f5fc;
  --ink:#1d1d1d;
  --rule:#c8ccd4;
}
*{margin:0;padding:0;box-sizing:border-box}
html,body{width:1200px;height:880px;overflow:hidden;background:#fff}
body{position:relative;font-family:'Poppins',sans-serif;color:var(--ink)}
.shapes{position:absolute;left:0;top:0}
.panel{position:absolute;left:0;top:150px;width:505px;height:715px;background:var(--panel)}
.abs{position:absolute}
.brand-name{left:75px;top:40px;font-size:24px;font-weight:600;color:var(--brand);line-height:1}
.headline{left:172px;top:42px;font-size:18.5px;font-weight:600;color:var(--brand);line-height:21px;letter-spacing:.3px}
.statements{left:0;top:95px;width:505px;text-align:center;font-size:8px;line-height:13px;text-transform:uppercase}
.level h3{font-size:14px;font-weight:400;line-height:16px;margin-bottom:3px;text-transform:uppercase}
.level p{font-size:7.4px;line-height:8.7px;text-align:justify}
.level.right{left:287px;width:171px}
.level.left{left:43px;width:170px}
.level.left h3{text-align:right}
.pill{position:absolute;background:var(--teal);color:#fff;font-size:10px;line-height:12px;height:12px;border-radius:6px;padding:0 6px;white-space:nowrap;text-transform:uppercase}
.pill.tall{height:25px;border-radius:12px;line-height:10.5px;padding:2px 10px}
.footer-name{left:884px;top:836px;font-size:20px;font-weight:600;color:var(--brand);line-height:1}
.footer-url{left:1000px;top:843px;font-size:12.5px;font-weight:600;color:var(--brand);line-height:1}
.badge-text{font-family:'Poppins',sans-serif;font-weight:600;fill:#fff}
</style>
</head>
<body>
<div class="panel"></div>

<svg class="shapes" width="1200" height="880" viewBox="0 0 1200 880">
  <!-- header mark -->
  <circle cx="46" cy="57" r="24" fill="var(--brand)"/>
  <line x1="506" y1="19" x2="506" y2="864" stroke="var(--rule)" stroke-width="2"/>

  <!-- KMV tube -->
  <rect x="239" y="188" width="26" height="557" rx="13" fill="var(--track)"/>
  <rect x="239" y="226" width="26" height="68" rx="13" fill="var(--pink)"/><rect x="239" y="260" width="26" height="34" fill="var(--pink)"/>
  <rect x="239" y="301" width="26" height="68" fill="var(--purple)"/>
  <rect x="239" y="376" width="26" height="68" fill="var(--yellow)"/>
  <rect x="239" y="451" width="26" height="68" fill="var(--orange)"/>
  <rect x="239" y="526" width="26" height="68" fill="var(--green)"/>
  <rect x="239" y="601" width="26" height="68" fill="var(--sky)"/>
  <rect x="239" y="676" width="26" height="69" rx="13" fill="var(--red)"/><rect x="239" y="676" width="26" height="34" fill="var(--red)"/>
  <circle cx="252" cy="720" r="3.5" fill="var(--teal)"/>
  <line x1="252" y1="720" x2="252" y2="766" stroke="var(--teal)" stroke-width="2"/>
  <circle cx="252" cy="798" r="32" fill="var(--brand)"/>
  <text x="252" y="806" text-anchor="middle" class="badge-text" font-size="22">KMV</text>

  <!-- level brackets -->
  <g stroke-width="1.2" fill="none">
    <path d="M281 229V294M265 256H281" stroke="var(--pink)"/>
    <path d="M220 302V369M239 329H220" stroke="var(--purple)"/>
    <path d="M281 377V444M265 404H281" stroke="var(--yellow)"/>
    <path d="M220 452V519M239 479H220" stroke="var(--orange)"/>
    <path d="M281 527V594M265 554H281" stroke="var(--green)"/>
    <path d="M220 602V669M239 629H220" stroke="var(--sky)"/>
    <path d="M281 677V745M265 704H281" stroke="var(--red)"/>
  </g>

  <!-- comparison tubes: top row -->
  <g>
    <rect x="581" y="101" width="26" height="237" rx="13" fill="var(--track)"/>
    <rect x="657" y="101" width="26" height="237" rx="13" fill="var(--track)"/>
    <rect x="734" y="101" width="26" height="237" rx="13" fill="var(--track)"/>
    <rect x="811" y="101" width="26" height="237" rx="13" fill="var(--track)"/>
    <rect x="888" y="101" width="26" height="237" rx="13" fill="var(--track)"/>
    <rect x="964" y="101" width="26" height="237" rx="13" fill="var(--track)"/>
    <rect x="1041" y="101" width="26" height="237" rx="13" fill="var(--track)"/>
    <rect x="1118" y="101" width="26" height="237" rx="13" fill="var(--track)"/>
    <!-- physical -->
    <g fill="var(--red)">
      <path d="M581 292H607V325A13 13 0 0 1 581 325Z"/>
      <path d="M657 292H683V325A13 13 0 0 1 657 325Z"/>
      <path d="M734 292H760V325A13 13 0 0 1 734 325Z"/>
      <path d="M811 292H837V325A13 13 0 0 1 811 325Z"/>
      <path d="M888 292H914V325A13 13 0 0 1 888 325Z"/>
      <path d="M964 292H990V325A13 13 0 0 1 964 325Z"/>
      <path d="M1041 292H1067V325A13 13 0 0 1 1041 325Z"/>
      <path d="M1118 292H1144V325A13 13 0 0 1 1118 325Z"/>
    </g>
    <rect x="657" y="239" width="26" height="47" fill="var(--sky)"/>
    <rect x="734" y="239" width="26" height="47" fill="var(--sky)"/>
    <rect x="734" y="186" width="26" height="47" fill="var(--orange)"/>
    <rect x="811" y="239" width="26" height="47" fill="var(--orange)"/>
    <rect x="888" y="239" width="26" height="47" fill="var(--pink)"/>
    <rect x="964" y="239" width="26" height="47" fill="var(--orange)"/>
    <rect x="964" y="186" width="26" height="47" fill="var(--pink)"/>
    <rect x="1041" y="239" width="26" height="47" fill="var(--yellow)"/>
    <rect x="1041" y="186" width="26" height="47" fill="var(--pink)"/>
    <rect x="1118" y="239" width="26" height="47" fill="var(--sky)"/>
    <rect x="1118" y="186" width="26" height="47" fill="var(--yellow)"/>
    <rect x="1118" y="133" width="26" height="47" fill="var(--pink)"/>
  </g>

  <!-- comparison tubes: bottom row -->
  <g>
    <rect x="581" y="528" width="26" height="237" rx="13" fill="var(--track)"/>
    <rect x="657" y="528" width="26" height="237" rx="13" fill="var(--track)"/>
    <rect x="734" y="528" width="26" height="237" rx="13" fill="var(--track)"/>
    <rect x="811" y="528" width="26" height="237" rx="13" fill="var(--track)"/>
    <rect x="888" y="528" width="26" height="237" rx="13" fill="var(--track)"/>
    <rect x="964" y="528" width="26" height="237" rx="13" fill="var(--track)"/>
    <rect x="1041" y="528" width="26" height="237" rx="13" fill="var(--track)"/>
    <rect x="1118" y="528" width="26" height="237" rx="13" fill="var(--track)"/>
    <path d="M581 718H607V752A13 13 0 0 1 581 752Z" fill="var(--red)"/>
    <path d="M657 718H683V752A13 13 0 0 1 657 752Z" fill="var(--sky)"/>
    <path d="M734 718H760V752A13 13 0 0 1 734 752Z" fill="var(--sky)"/>
    <path d="M811 718H837V752A13 13 0 0 1 811 752Z" fill="var(--sky)"/>
    <path d="M888 718H914V752A13 13 0 0 1 888 752Z" fill="var(--sky)"/>
    <path d="M964 718H990V752A13 13 0 0 1 964 752Z" fill="var(--orange)"/>
    <path d="M1041 718H1067V752A13 13 0 0 1 1041 752Z" fill="var(--orange)"/>
    <path d="M1118 718H1144V752A13 13 0 0 1 1118 752Z" fill="var(--yellow)"/>
    <rect x="581" y="665" width="26" height="47" fill="var(--orange)"/>
    <rect x="581" y="613" width="26" height="47" fill="var(--yellow)"/>
    <rect x="581" y="560" width="26" height="47" fill="var(--pink)"/>
    <rect x="734" y="665" width="26" height="47" fill="var(--pink)"/>
    <rect x="811" y="665" width="26" height="47" fill="var(--yellow)"/>
    <rect x="888" y="665" width="26" height="47" fill="var(--yellow)"/>
    <rect x="888" y="613" width="26" height="47" fill="var(--pink)"/>
    <rect x="1041" y="665" width="26" height="47" fill="var(--pink)"/>
    <rect x="1118" y="665" width="26" height="47" fill="var(--purple)"/>
  </g>

  <!-- connectors -->
  <g stroke="var(--teal)" stroke-width="1.6" fill="var(--teal)">
    <line x1="670" y1="70" x2="670" y2="118"/><circle cx="670" cy="118" r="3.2"/>
    <line x1="824" y1="70" x2="824" y2="118"/><circle cx="824" cy="118" r="3.2"/>
    <line x1="977" y1="70" x2="977" y2="118"/><circle cx="977" cy="118" r="3.2"/>
    <line x1="1131" y1="70" x2="1131" y2="118"/><circle cx="1131" cy="118" r="3.2"/>
    <line x1="594" y1="307" x2="594" y2="356"/><circle cx="594" cy="307" r="3.2"/>
    <line x1="747" y1="307" x2="747" y2="352"/><circle cx="747" cy="307" r="3.2"/>
    <line x1="901" y1="307" x2="901" y2="356"/><circle cx="901" cy="307" r="3.2"/>
    <line x1="1054" y1="307" x2="1054" y2="352"/><circle cx="1054" cy="307" r="3.2"/>
    <line x1="670" y1="497" x2="670" y2="545"/><circle cx="670" cy="545" r="3.2"/>
    <line x1="824" y1="497" x2="824" y2="545"/><circle cx="824" cy="545" r="3.2"/>
    <line x1="977" y1="497" x2="977" y2="545"/><circle cx="977" cy="545" r="3.2"/>
    <line x1="1131" y1="497" x2="1131" y2="545"/><circle cx="1131" cy="545" r="3.2"/>
    <line x1="594" y1="733" x2="594" y2="782"/><circle cx="594" cy="733" r="3.2"/>
    <line x1="747" y1="733" x2="747" y2="778"/><circle cx="747" cy="733" r="3.2"/>
    <line x1="901" y1="733" x2="901" y2="781"/><circle cx="901" cy="733" r="3.2"/>
    <line x1="1054" y1="733" x2="1054" y2="777"/><circle cx="1054" cy="733" r="3.2"/>
  </g>

  <!-- footer -->
  <circle cx="866" cy="850" r="10" fill="var(--brand)"/>
  <line x1="990" y1="838" x2="990" y2="862" stroke="var(--brand)" stroke-width="1.2"/>
</svg>

<div class="abs brand-name">KMV</div>
<div class="abs headline">CHOOSE KMV FOR FAST, IMMEDIATE<br>AND POWERFUL RESULTS</div>
<div class="abs statements">
  I must experience healing on all levels, I am not just a body.<br>
  I want to learn how to heal myself, so I'm not dependent on others.<br>
  I want to release all my emotional and mental blocks, so I can be the best version of myself.
</div>

<section class="abs level right" style="top:226px">
  <h3 style="color:var(--pink)">Before &amp; After Testing</h3>
  <p>KMV is the only modality the enables you to provide before and after results, which are documented by us, and analysed by you with our help.</p>
</section>
<section class="abs level left" style="top:300px">
  <h3 style="color:var(--purple)">Superconscious</h3>
  <p>KMV is the only modality the enables you to access and heal your superconscious mind yourself.</p>
</section>
<section class="abs level right" style="top:374px">
  <h3 style="color:var(--yellow)">Subconscious</h3>
  <p>Some modalities, like Kinesiology, access your subconscious through muscle testing. KMV empowers you to access your own subconscious and heal it yourself.</p>
</section>
<section class="abs level left" style="top:451px">
  <h3 style="color:var(--orange)">Energetic</h3>
  <p>Most modalities try to move the energy in your body for you. KMV enables and empowers you to do it yourself.</p>
</section>
<section class="abs level right" style="top:526px">
  <h3 style="color:var(--green)">Emotional</h3>
  <p>KMV is the only modality that engages your emotions on a physical level. Emotions get stuck in your body and can cause illness over time if left unchecked. KMV enables you you experience fast and powerful emotional releasing</p>
</section>
<section class="abs level left" style="top:601px">
  <h3 style="color:var(--sky)">Mental</h3>
  <p>KMV enables you to use your own consciousness to self-heal. We don't give you advice or coaching, we allow your mind to heal itself.</p>
</section>
<section class="abs level right" style="top:672px">
  <h3 style="color:var(--red)">Physical</h3>
  <p>Most modalities, including, a western medicine, focus on and treat the physical body only. The KMV process enables you to engage in healing your own body during the session. There is no muscle testing, no hands-on healing and no herbal remedies or medicines.</p>
</section>

<!-- modality labels -->
<div class="pill" style="left:612px;top:58px;width:117px;text-align:center">Psychic Intuitive</div>
<div class="pill" style="left:778px;top:58px;width:92px;text-align:center">Acupuncture</div>
<div class="pill" style="left:925px;top:58px;width:105px;text-align:center">Chinese Medicine</div>
<div class="pill" style="left:1113px;top:58px;width:36px;text-align:center">EFT</div>

<div class="pill" style="left:535px;top:355px;width:118px">Massage</div>
<div class="pill" style="left:535px;top:371px;width:118px">Yoga</div>
<div class="pill" style="left:535px;top:386px;width:118px">Natropathy</div>
<div class="pill" style="left:535px;top:402px;width:118px">Ayurvedic Medicine</div>
<div class="pill" style="left:535px;top:418px;width:118px">Western Medicine</div>
<div class="pill tall" style="left:697px;top:352px;width:100px">Family<br>Constellation</div>
<div class="pill" style="left:840px;top:355px;width:121px">Nutritional Healing</div>
<div class="pill" style="left:1006px;top:351px;width:96px">Kinesiology</div>
<div class="pill" style="left:1006px;top:366px;width:96px">Bowen Therapy</div>

<div class="pill" style="left:624px;top:485px;width:96px;text-align:center">Pshychology</div>
<div class="pill" style="left:769px;top:469px;width:116px">Hypnotheraphy</div>
<div class="pill" style="left:769px;top:485px;width:116px">Inner Child Healing</div>
<div class="pill" style="left:926px;top:469px;width:104px">Reiki</div>
<div class="pill" style="left:926px;top:485px;width:104px">Crystal Healing</div>
<div class="pill" style="left:1082px;top:485px;width:95px;text-align:center">Theta Healing</div>

<div class="pill" style="left:550px;top:782px;width:87px;text-align:center">Chiropractic</div>
<div class="pill tall" style="left:700px;top:778px;width:100px">Mindfullness<br>Meditation</div>
<div class="pill" style="left:700px;top:808px;width:100px">Life Coaching</div>
<div class="pill" style="left:850px;top:781px;width:108px">NLP</div>
<div class="pill" style="left:850px;top:797px;width:108px">Timeline Theraphy</div>
<div class="pill" style="left:1004px;top:777px;width:101px;text-align:center">Energy Medicine</div>

<div class="abs footer-name">Lumenwell</div>
<div class="abs footer-url">www.lumenwell.com.au</div>
</body>
</html>
```